Personal Injury Lawyer Billboard

I would like a design created featuring the image of the lawyer centered in the middle of the design.
To the left of the lawyer's image it should read "INJURED?"
To the right of the lawyer's image, it should read "CALL DEAN!"
Under Call Dean, include the phone number 318-555-0187.
At the bottom of the design include the lawyers information "Dean Marlowe Accident & Injury Lawyers"
PLEASE REMOVED THE BACKGROUND IMAGERY OF THE PHOTO SUBMITTED. Also, the colors for this design should match the colors shown in the logo (navy, white and relective soft gold). Please use those color combinations in ways that best stand out.

```html
<!DOCTYPE html>
<html lang="en">
<head>
<meta charset="utf-8">
<title>Dean Marlowe Accident &amp; Injury Lawyers – Billboard</title>
<link rel="stylesheet" href="https://fonts.googleapis.com/css2?family=Archivo:wdth,wght@62..125,700..900&family=Oswald:wght@500&display=swap">
<style>
  :root {
    --navy: #0b1b45;
    --gold: #bf9a2f;
    --white: #ffffff;
    --stage: #cfcfcf;
    --suit-top: #3a4a7a;
    --suit-bottom: #16224d;
  }
  html, body {
    margin: 0;
    padding: 0;
    width: 1020px;
    height: 1200px;
    overflow: hidden;
    background: var(--stage);
  }
  .billboard {
    position: absolute;
    left: 40px;
    top: 365px;
    width: 940px;
    height: 470px;
    display: block;
    box-shadow: 0 12px 30px rgba(0, 0, 0, 0.25);
  }
  .headline {
    font-family: "Archivo", "Arial Black", sans-serif;
    font-weight: 900;
    font-stretch: 110%;
    fill: var(--gold);
  }
  .call-to-action {
    font-family: "Archivo", "Arial Black", sans-serif;
    font-weight: 900;
    font-stretch: 90%;
    fill: var(--white);
  }
  .firm-name {
    font-family: "Oswald", "Arial Narrow", sans-serif;
    font-weight: 500;
    fill: var(--white);
  }
  .phone-number {
    font-family: "Archivo", "Arial Black", sans-serif;
    font-weight: 800;
    font-stretch: 125%;
    fill: var(--navy);
  }
</style>
</head>
<body>
  <svg class="billboard" viewBox="0 0 940 470" xmlns="http://www.w3.org/2000/svg">
    <defs>
      <linearGradient id="portrait-tone" x1="0" y1="0" x2="0" y2="1">
        <stop offset="0" stop-color="var(--suit-top)"/>
        <stop offset="1" stop-color="var(--suit-bottom)"/>
      </linearGradient>
    </defs>

    <rect class="panel" width="940" height="359" fill="var(--navy)"/>
    <rect class="phone-band" y="359" width="940" height="111" fill="var(--gold)"/>

    <text class="headline" x="48" y="192" font-size="216"
          textLength="846" lengthAdjust="spacingAndGlyphs">INJURED?</text>

    <rect class="lawyer-portrait" x="482" y="138" width="199" height="221"
          rx="6" fill="url(#portrait-tone)"
          role="img" aria-label="Portrait of attorney Dean Marlowe in a navy suit, smiling with a raised fist"/>

    <text class="firm-name" x="52" y="277" font-size="72"
          textLength="362" lengthAdjust="spacingAndGlyphs">DEAN MARLOWE</text>
    <text class="firm-name" x="52" y="336" font-size="44"
          textLength="362" lengthAdjust="spacingAndGlyphs">ACCIDENT &amp; INJURY LAWYERS</text>

    <text class="call-to-action" x="886" y="274" font-size="74" text-anchor="end"
          textLength="148" lengthAdjust="spacingAndGlyphs">CALL</text>
    <text class="call-to-action" x="884" y="342" font-size="86" text-anchor="end"
          textLength="180" lengthAdjust="spacingAndGlyphs">DEAN!</text>

    <text class="phone-number" x="43" y="445" font-size="86"
          textLength="855" lengthAdjust="spacingAndGlyphs">318-555-0187</text>
  </svg>
</body>
</html>
```